Web page for a garment manufacturing company

We are clothing manufacturer based in Romania.
With our recent expansion, we have significantly increased our internal capacity, allowing us to take on new partnerships and deliver high-quality production services.
Our expertise includes producing classic coats, blazers, trousers, skirts, dresses, and blouses, though we are flexible and open to working with various other textile products.

Target Market(s)

High-end market and luxury

Industry/Entity Type

Garments Manufacturer

Coding

Coded - Design and coding required

Number of Pages Required

1 page

Colors

Designer to choose only greyscale colors for use in the design.

Requirements
Must have
• Velmora logo from our presentation
Nice to have
• https://www.lorvani.pt/
Should not have
• prices, wedding dresses, collections

```html
<!DOCTYPE html>
<html lang="en">
<head>
<meta charset="utf-8">
<title>Velmora — Clothing Manufacturer</title>
<link href="https://fonts.googleapis.com/css2?family=Bebas+Neue&family=Roboto:wght@400;500;700&display=swap" rel="stylesheet">
<style>
:root{
  --ink:#111418;
  --slate:#3e4c5c;
  --slate-mid:#6f8298;
  --slate-soft:#8a9bb0;
  --pale:#eaf1f9;
  --white:#ffffff;
  --text:#5a5f66;
  --footer:#121212;
}
*{box-sizing:border-box;margin:0;padding:0}
html,body{width:1200px;height:3621px;overflow:hidden}
body{font-family:'Roboto',sans-serif;color:var(--ink);background:var(--white);position:relative}
.display{font-family:'Bebas Neue',sans-serif;font-weight:400;letter-spacing:.5px}
.abs{position:absolute}
.btn{position:absolute;display:flex;align-items:center;justify-content:center;gap:8px;border-radius:30px;font-size:14px;font-weight:700;text-transform:uppercase;color:var(--white)}
.btn svg{width:13px;height:13px}
.btn-solid{background:var(--slate)}
.btn-ghost{border:2px solid var(--white);background:rgba(62,76,92,.35)}
.section-title{position:absolute;left:0;width:1200px;text-align:center;font-size:56px;line-height:1}
.section-title .soft{color:var(--slate-mid)}

/* hero */
.hero{position:absolute;left:0;top:0;width:1200px;height:496px;background:linear-gradient(90deg,#6b5a4e 0%,#c7b8a6 22%,#8b7564 34%,#2a2622 55%,#17151a 100%)}
.logo{font-size:34px;color:var(--white)}
.nav a{position:absolute;top:29px;font-size:14px;font-weight:700;color:var(--white);text-decoration:none}
.nav .active{text-decoration:underline;text-underline-offset:4px}
.hero-title{left:607px;top:95px;font-size:76px;line-height:78px;color:var(--white)}
.hero-title .soft{color:var(--slate-soft)}
.hero-sub{left:680px;top:340px;font-size:24px;font-weight:500;color:var(--white)}
.dots span{position:absolute;left:1126px;width:8px;height:8px;border-radius:50%;background:var(--slate-soft)}

/* capacity */
.cap{position:absolute;top:496px;height:156px;width:600px}
.cap h3{position:absolute;top:44px;font-size:40px;color:var(--white)}
.cap p{position:absolute;top:47px;color:var(--white);font-size:17px;font-weight:500;line-height:22px}
.cap p b{font-size:24px;font-weight:500}

/* expertise */
.card{position:absolute;top:854px;width:224px;height:242px;border-radius:6px}
.card.lift{background:var(--white);box-shadow:0 6px 24px rgba(0,0,0,.1)}
.card .art{position:absolute;left:37px;top:22px;width:150px;height:140px;border-radius:10px}
.card .label{position:absolute;left:0;bottom:0;width:224px;height:62px;border-radius:6px;display:flex;align-items:center;justify-content:center;font-size:16px;font-weight:500;text-transform:uppercase}
.arrow{position:absolute;width:44px;height:44px;border-radius:50%;display:flex;align-items:center;justify-content:center}
.arrow.dark{background:var(--slate-mid)}
.arrow.light{background:#dde6f1}

/* about */
.about{position:absolute;left:0;top:1276px;width:1200px;height:567px;background:var(--pale)}
.about-photo{position:absolute;left:142px;top:80px;width:405px;height:405px;border-radius:6px;background:linear-gradient(135deg,#3a4256 0%,#7b6a5c 45%,#a9a59c 75%,#6f5a4b 100%)}
.badge{position:absolute;left:443px;top:284px;width:146px;height:152px;background:var(--slate);border:6px solid var(--white);border-radius:6px;color:var(--white);text-align:center}
.badge small{display:block;margin-top:34px;font-size:17px}
.badge strong{display:block;margin-top:8px;font-size:36px;font-weight:500}
.about h2{position:absolute;left:642px;top:92px;font-size:54px;line-height:1}
.about h2 .soft{color:var(--slate-mid)}
.about p{position:absolute;left:642px;width:420px;font-size:14px;line-height:26px;color:var(--text)}

/* certifications */
.cert{position:absolute;top:2003px;height:76px;border-radius:8px;background:#d9dee5}
.cdots span{position:absolute;top:2113px;width:7px;height:7px;border-radius:50%;background:#b6c0cc}

/* partnership */
.partner{position:absolute;left:0;top:2200px;width:1200px;height:515px;background:var(--slate)}
.partner h2{position:absolute;left:146px;top:94px;font-size:54px;color:var(--white);line-height:1}
.partner p{position:absolute;left:146px;width:425px;font-size:15px;line-height:26px;color:var(--white)}
.pic{position:absolute;border:8px solid var(--white);box-shadow:0 10px 30px rgba(0,0,0,.35)}

/* testimonials */
.tcard{position:absolute;top:2901px;width:285px;height:229px;background:var(--white);border-radius:8px;box-shadow:0 6px 24px rgba(0,0,0,.07)}
.tcard .avatar{position:absolute;left:16px;top:20px;width:62px;height:62px;border-radius:50%;background:linear-gradient(160deg,#6f7785,#2c323b)}
.tcard h4{position:absolute;left:96px;top:38px;font-size:12px;font-weight:500;text-transform:uppercase}
.tcard .role{position:absolute;left:96px;top:58px;font-size:11px;color:var(--slate)}
.tcard p{position:absolute;left:22px;top:100px;width:250px;font-size:11.5px;line-height:19.5px;color:#777}

/* footer */
.footer{position:absolute;left:0;top:3217px;width:1200px;height:404px;background:var(--footer);color:var(--white)}
.footer h5{position:absolute;top:80px;font-size:16px;font-weight:500;text-transform:uppercase}
.footer ul{position:absolute;top:115px;list-style:none;font-size:14px;line-height:25.7px}
.footer .intro{position:absolute;left:110px;top:145px;font-size:14px;line-height:25.7px}
.footer .rule{position:absolute;left:219px;top:302px;width:762px;height:1px;background:#555}
.footer .copy{position:absolute;left:0;top:332px;width:1200px;text-align:center;font-size:14px}
</style>
</head>
<body>

<!-- Hero -->
<section class="hero" role="img" aria-label="Photo of a man in a cream wool coat and brown scarf on a blurred city street at dusk"></section>
<div class="abs logo display" style="left:112px;top:18px">VELMORA</div>
<nav class="nav">
  <a class="active" style="left:566px">HOME</a>
  <a style="left:632px">ABOUT</a>
  <a style="left:705px">SERVICE</a>
  <a style="left:789px">PARTNERSHIP</a>
</nav>
<div class="btn btn-ghost" style="left:920px;top:15px;width:168px;height:50px">Contact us</div>
<h1 class="abs hero-title display"><span class="soft">Romania's</span> Premier<br>Clothing<br>Manufacturer.</h1>
<div class="abs hero-sub">Quality. Flexibility. Expertise</div>
<div class="btn btn-ghost" style="left:759px;top:402px;width:225px;height:50px">Partner with us
  <svg viewBox="0 0 16 16"><circle cx="8" cy="8" r="8" fill="#fff"/><path d="M6.5 4.5 10 8l-3.5 3.5" stroke="#3e4c5c" stroke-width="2" fill="none"/></svg></div>
<div class="dots"><span style="top:226px"></span><span style="top:240px"></span><span style="top:254px"></span><span style="top:268px;background:#fff"></span></div>

<!-- Capacity -->
<div class="cap" style="left:0;background:var(--slate)">
  <h3 class="display" style="left:113px">Ladies' Garments</h3>
  <p style="left:427px"><b>75 %</b><br>of the capacity</p>
</div>
<div class="cap" style="left:596px;width:604px;background:var(--slate-mid)">
  <h3 class="display" style="left:48px">Men's Garments</h3>
  <p style="left:374px"><b>25 %</b><br>of the capacity</p>
</div>

<!-- Expertise -->
<h2 class="section-title display" style="top:755px"><span class="soft">Our</span> Expertise</h2>
<div class="arrow dark" style="left:42px;top:949px"><svg width="14" height="14" viewBox="0 0 14 14"><path d="M7 3 3 7l4 4M11 3 7 7l4 4" stroke="#fff" stroke-width="1.6" fill="none"/></svg></div>
<div class="arrow light" style="left:1113px;top:949px"><svg width="14" height="14" viewBox="0 0 14 14"><path d="M3 3l4 4-4 4M7 3l4 4-4 4" stroke="#6f8298" stroke-width="1.6" fill="none"/></svg></div>
<div class="card" style="left:108px"><div class="art" role="img" aria-label="Illustration of a blue blouse" style="background:#9fd3ef"></div><div class="label" style="background:#fbeeee">Blouses</div></div>
<div class="card" style="left:360px"><div class="art" role="img" aria-label="Illustration of a classic coat" style="background:#cdebf7"></div><div class="label" style="background:#dcf1f6">Classic coats</div></div>
<div class="card lift" style="left:611px"><div class="art" role="img" aria-label="Illustration of a pleated skirt" style="background:#8fd0ef"></div><div class="label" style="background:#e6f4e6">Skirts</div></div>
<div class="card" style="left:863px"><div class="art" role="img" aria-label="Illustration of a blazer" style="background:#bfe2f2"></div><div class="label" style="background:#fcf4e6">Blazers</div></div>
<div class="btn btn-solid" style="left:477px;top:1131px;width:246px;height:48px">Explore our services
  <svg viewBox="0 0 16 16"><circle cx="8" cy="8" r="8" fill="#fff"/><path d="M6.5 4.5 10 8l-3.5 3.5" stroke="#3e4c5c" stroke-width="2" fill="none"/></svg></div>

<!-- About -->
<section class="about">
  <div class="about-photo" role="img" aria-label="Aerial photo of the factory buildings with solar panels on the roofs"></div>
  <div class="badge"><small>Established in</small><strong>2005</strong></div>
  <h2 class="display">About <span class="soft">Us</span></h2>
  <p style="top:165px">VELMORA is a manufacturing company for Ready-to-wear, situated in Valdera, a city with a rich tradition in the clothing industry. The top management is international, and we are proud to have a diverse and dynamic group of professionals from different countries working together.</p>
  <p style="top:319px">With our optimistic team spirit and passion for high-quality productions, we are ready to take on new challenges and delight our clients with very good results.</p>
  <div class="btn btn-solid" style="left:642px;top:422px;width:164px;height:48px">Learn more
    <svg viewBox="0 0 16 16"><circle cx="8" cy="8" r="8" fill="#fff"/><path d="M6.5 4.5 10 8l-3.5 3.5" stroke="#3e4c5c" stroke-width="2" fill="none"/></svg></div>
</section>

<!-- Certifications -->
<h2 class="section-title display" style="top:1914px"><span class="soft">Our</span> Certifications</h2>
<div class="cert" style="left:142px;width:92px" role="img" aria-label="Environmental management certificate badge"></div>
<div class="cert" style="left:342px;width:112px;height:40px;top:2022px" role="img" aria-label="Social compliance certificate badge"></div>
<div class="cert" style="left:540px;width:140px;height:70px;top:2008px" role="img" aria-label="Recycled material standard badge"></div>
<div class="cert" style="left:760px;width:110px;height:34px;top:2020px" role="img" aria-label="Trade association membership badge"></div>
<div class="cert" style="left:994px;width:68px;height:68px;top:2008px;border-radius:50%" role="img" aria-label="Organic content standard badge"></div>
<div class="cdots"><span style="left:585px"></span><span style="left:596px;background:var(--slate)"></span><span style="left:607px"></span></div>

<!-- Partnership -->
<section class="partner">
  <h2 class="display">Our Partnership</h2>
  <p style="top:166px">Lorem ipsum dolor sit amet, consectetur adipiscing elit, sed do eiusmod tempor incididunt ut labore et dolore magna aliqua. Ut enim ad minim veniam, quis nostrud exercitation ullamco laboris nisi ut aliquip ex ea commodo consequat. Duis aute irure dolor in reprehenderit in voluptate velit esse cillum dolore</p>
  <p style="top:304px">Lorem ipsum dolor sit amet, consectetur adipiscing elit, sed do eiusmod tempor incididunt ut labore</p>
  <div class="btn btn-ghost" style="left:146px;top:370px;width:166px;height:50px;background:transparent">Learn more
    <svg viewBox="0 0 16 16"><circle cx="8" cy="8" r="8" fill="#fff"/><path d="M6.5 4.5 10 8l-3.5 3.5" stroke="#3e4c5c" stroke-width="2" fill="none"/></svg></div>
  <div class="pic" role="img" aria-label="Photo of a bright open-plan office interior" style="left:640px;top:68px;width:230px;height:265px;transform:rotate(-12deg);background:linear-gradient(150deg,#8a6a50,#d8cfc2 55%,#5e4838)"></div>
  <div class="pic" role="img" aria-label="Photo of staff working at desks in the design studio" style="left:815px;top:108px;width:240px;height:270px;transform:rotate(32deg);background:linear-gradient(160deg,#7a4a38,#c9c3bb 50%,#3f5e8a 80%,#a33)"></div>
</section>

<!-- Testimonials -->
<h2 class="section-title display" style="top:2801px"><span class="soft">Our</span> Testimonials</h2>
<div class="arrow dark" style="left:42px;top:2975px"><svg width="14" height="14" viewBox="0 0 14 14"><path d="M7 3 3 7l4 4M11 3 7 7l4 4" stroke="#fff" stroke-width="1.6" fill="none"/></svg></div>
<div class="arrow light" style="left:1113px;top:2975px"><svg width="14" height="14" viewBox="0 0 14 14"><path d="M3 3l4 4-4 4M7 3l4 4-4 4" stroke="#6f8298" stroke-width="1.6" fill="none"/></svg></div>
<div class="tcard" style="left:131px"><div class="avatar" role="img" aria-label="Client portrait photo"></div><h4>Dana Morrow</h4><div class="role">Lorum Ipsum Dolor</div><p>Lorem ipsum dolor sit amet, consectetur adipiscing elit, sed do eiusmod tempor incididunt ut labore et dolore magna aliqua. Ut enim ad minim veniam, quis nostrud exercitation ullamco laboris</p></div>
<div class="tcard" style="left:457px"><div class="avatar" role="img" aria-label="Client portrait photo"></div><h4>Dana Morrow</h4><div class="role">Lorum Ipsum Dolor</div><p>Lorem ipsum dolor sit amet, consectetur adipiscing elit, sed do eiusmod tempor incididunt ut labore et dolore magna aliqua. Ut enim ad minim veniam, quis nostrud exercitation ullamco laboris</p></div>
<div class="tcard" style="left:783px"><div class="avatar" role="img" aria-label="Client portrait photo"></div><h4>Dana Morrow</h4><div class="role">Lorum Ipsum Dolor</div><p>Lorem ipsum dolor sit amet, consectetur adipiscing elit, sed do eiusmod tempor incididunt ut labore et dolore magna aliqua. Ut enim ad minim veniam, quis nostrud exercitation ullamco laboris</p></div>

<!-- Footer -->
<footer class="footer">
  <div class="abs logo display" style="left:110px;top:86px;font-size:32px">VELMORA</div>
  <div class="intro">Established in 2005 as a Joint<br>Venture between a local manufacturer<br>&nbsp;and a foreign investor.</div>
  <div class="abs" style="left:114px;top:234px;font-size:14px">f &nbsp;|&nbsp; ig &nbsp;|&nbsp; in</div>
  <h5 style="left:453px">Quick Links</h5>
  <ul style="left:453px"><li>Home</li><li>About</li><li>Service</li><li>Partnership</li><li>Contact Us</li></ul>
  <h5 style="left:667px">Other Links</h5>
  <ul style="left:667px"><li>Merchandisers</li><li>Warehouse</li><li>Laboratory</li><li>Cutting room</li><li>Sewing</li><li>Finishing</li></ul>
  <h5 style="left:881px">Contact Us</h5>
  <ul style="left:881px"><li>ROMANIA .Valdera</li><li>Str. Ardelean 48,</li><li>Zip code: 610457</li><li>Phone +40 300 555 014</li><li>Fax +40 300 555 029</li><li>Email: info@velmora-wear.com</li></ul>
  <div class="rule"></div>
  <div class="copy">Copyright@2024 - All Rights Reserved By Velmora</div>
</footer>

</body>
</html>
```